KRT Project Signage

Need a sign to be displayed in the front of properties currently under Construction or Renovation to advertise our company information. Need it to be Professional and Contemporary. We are a Design/Build Construction Company. Information should include Company Name, email, website, phone number. Attached: Logo and company brochure, also included and inspiration images

```html
<!DOCTYPE html>
<html lang="en">
<head>
<meta charset="utf-8">
<title>KRT Construction – Project Sign</title>
<link rel="stylesheet" href="https://fonts.googleapis.com/css2?family=Poppins:wght@500;600;700&display=swap">
<style>
  :root {
    --ink: #000000;
    --paper: #ffffff;
    --stage: #f2f2f2;
    --accent: #f2e63a;
    --shade: #a8a8a8;
    --icon-grey: #b9b9b9;
  }
  * { margin: 0; padding: 0; box-sizing: border-box; }
  html, body {
    width: 1200px;
    height: 3455px;
    overflow: hidden;
    background: var(--stage);
    font-family: "Poppins", sans-serif;
  }
  .sign {
    position: absolute;
    left: 100px;
    top: 977px;
    width: 1000px;
    height: 1501px;
    background: var(--ink);
    overflow: hidden;
    box-shadow: 0 14px 40px rgba(0, 0, 0, 0.35);
  }
  .sign__shapes {
    position: absolute;
    inset: 0;
    width: 1000px;
    height: 1501px;
  }
  .line {
    position: absolute;
    left: 0;
    width: 100%;
    text-align: center;
    white-space: nowrap;
  }
  .brand {
    top: 165px;
    display: flex;
    justify-content: center;
    align-items: center;
    gap: 22px;
  }
  .brand__dot {
    width: 44px;
    height: 44px;
    border-radius: 50%;
    background: var(--accent);
  }
  .brand__name {
    font-size: 58px;
    font-weight: 600;
    color: var(--ink);
    letter-spacing: 2px;
  }
  .brand__tagline {
    top: 258px;
    font-size: 30px;
    font-weight: 500;
    letter-spacing: 4px;
    color: var(--ink);
  }
  .brand__web {
    top: 318px;
    font-size: 30px;
    font-weight: 600;
    color: var(--ink);
  }
  .phone-box {
    position: absolute;
    left: 76px;
    top: 467px;
    width: 846px;
    height: 141px;
    border: 5px solid var(--paper);
    border-radius: 28px;
    background: var(--ink);
    display: flex;
    align-items: center;
    justify-content: center;
    gap: 34px;
  }
  .phone-box__number {
    font-size: 100px;
    font-weight: 700;
    color: var(--paper);
    letter-spacing: 1px;
  }
  .icon {
    position: absolute;
    left: 50%;
    transform: translateX(-50%);
  }
  .fax-icon { top: 643px; }
  .mail-icon { top: 855px; }
  .pin-icon { top: 1032px; }
  .fax-number {
    top: 745px;
    font-size: 74px;
    font-weight: 700;
    color: var(--paper);
  }
  .email {
    top: 942px;
    font-size: 48px;
    font-weight: 500;
    color: var(--paper);
  }
  .address {
    top: 1118px;
    font-size: 46px;
    font-weight: 600;
    line-height: 58px;
    color: var(--paper);
  }
  .footer-web {
    top: 1378px;
    font-size: 62px;
    font-weight: 700;
    color: var(--ink);
  }
</style>
</head>
<body>
  <main class="sign">
    <svg class="sign__shapes" viewBox="0 0 1000 1501" aria-hidden="true">
      <path fill="var(--shade)" d="M0 0 H1000 V225 C960 400 760 500 500 500 C240 500 40 400 0 205 Z"/>
      <path fill="var(--paper)" d="M0 0 H1000 V195 C960 375 760 476 500 476 C240 476 40 375 0 180 Z"/>
      <path fill="var(--shade)" d="M0 1390 C220 1300 420 1272 620 1275 C800 1278 930 1310 1000 1350 V1501 H0 Z"/>
      <path fill="var(--paper)" d="M0 1410 C220 1322 420 1295 620 1298 C800 1301 930 1335 1000 1378 V1501 H0 Z"/>
    </svg>

    <div class="line brand">
      <span class="brand__dot"></span>
      <span class="brand__name">KRT CONSTRUCTION</span>
    </div>
    <div class="line brand__tagline">LUXURY RENOVATIONS</div>
    <div class="line brand__web">www.krtconstruction.com</div>

    <div class="phone-box">
      <svg width="66" height="66" viewBox="0 0 24 24" aria-hidden="true">
        <path fill="var(--accent)" d="M6.6 10.8a15.1 15.1 0 0 0 6.6 6.6l2.2-2.2a1 1 0 0 1 1-.25 11.4 11.4 0 0 0 3.6.57 1 1 0 0 1 1 1V20a1 1 0 0 1-1 1A17 17 0 0 1 3 4a1 1 0 0 1 1-1h3.5a1 1 0 0 1 1 1c0 1.25.2 2.45.57 3.57a1 1 0 0 1-.25 1z"/>
        <path fill="none" stroke="var(--accent)" stroke-width="1.8" stroke-linecap="round" d="M14 3.5a7 7 0 0 1 6.5 6.5M14 7a3.5 3.5 0 0 1 3 3"/>
      </svg>
      <span class="phone-box__number">555.014.2280</span>
    </div>

    <svg class="icon fax-icon" width="70" height="76" viewBox="0 0 70 76" aria-hidden="true">
      <rect x="2" y="22" width="14" height="52" rx="4" fill="var(--icon-grey)"/>
      <rect x="20" y="2" width="34" height="24" fill="var(--icon-grey)"/>
      <rect x="20" y="28" width="48" height="46" rx="4" fill="var(--icon-grey)"/>
      <g fill="var(--ink)">
        <rect x="26" y="34" width="36" height="8"/>
        <rect x="27" y="48" width="8" height="6"/><rect x="40" y="48" width="8" height="6"/><rect x="53" y="48" width="8" height="6"/>
        <rect x="27" y="60" width="8" height="6"/><rect x="40" y="60" width="8" height="6"/><rect x="53" y="60" width="8" height="6"/>
      </g>
    </svg>
    <div class="line fax-number">555.014.7391</div>

    <svg class="icon mail-icon" width="76" height="66" viewBox="0 0 76 66" aria-hidden="true">
      <path fill="var(--icon-grey)" d="M2 26 L38 2 L74 26 V64 H2 Z"/>
      <rect x="16" y="8" width="44" height="34" fill="var(--paper)"/>
      <circle cx="38" cy="24" r="9" fill="none" stroke="var(--ink)" stroke-width="3"/>
      <path fill="var(--icon-grey)" d="M2 28 L38 50 L74 28 V64 H2 Z" stroke="var(--ink)" stroke-width="2"/>
      <path d="M2 64 L30 44 M74 64 L46 44" stroke="var(--ink)" stroke-width="2"/>
    </svg>
    <div class="line email">info@krtconstruction.com</div>

    <svg class="icon pin-icon" width="76" height="70" viewBox="0 0 76 70" aria-hidden="true">
      <ellipse cx="38" cy="58" rx="34" ry="10" fill="none" stroke="var(--icon-grey)" stroke-width="5"/>
      <path fill="var(--icon-grey)" d="M38 2 a20 20 0 0 1 20 20 c0 14 -20 36 -20 36 s-20 -22 -20 -36 a20 20 0 0 1 20 -20 z"/>
      <circle cx="38" cy="21" r="7" fill="var(--ink)"/>
    </svg>
    <div class="line address">1480 Harbor View Rd.<br>Suite 310 Coral Bay, FL 33000</div>

    <div class="line footer-web">www.krtconstruction.com</div>
  </main>
</body>
</html>
```